Flag Order

We were just looking to order some branding flags to put on our rental equipment for our business. We would like different examples of the colors, shapes, sizes, backgrounds etc. Was thinking of just doing the plains icon instead of the whole logo on there. but open to ideas. preferably not a white background as they could get dirty,

```html
<!DOCTYPE html>
<html lang="en">
<head>
<meta charset="utf-8">
<title>Flag Designs</title>
<link rel="stylesheet" href="https://fonts.googleapis.com/css2?family=Roboto:wght@400;900&display=swap">
<style>
  :root {
    --paper: #ffffff;
    --ink: #000000;
    --brand-blue: #1a7ad0;
    --blue-mid: #3b8ad6;
    --blue-light: #8dbbe8;
    --label-grey: #8a8a8a;
    --edge-grey: #7a7a7a;
    --stand-grey: #6f6f6f;
  }
  html, body {
    margin: 0;
    padding: 0;
    width: 1200px;
    height: 800px;
    overflow: hidden;
    background: var(--paper);
  }
  .board {
    position: relative;
    width: 1200px;
    height: 800px;
  }
  .design-label {
    position: absolute;
    top: 94px;
    width: 200px;
    margin: 0;
    text-align: center;
    font-family: "Roboto", Arial, sans-serif;
    font-weight: 400;
    font-size: 10px;
    letter-spacing: 3px;
    color: var(--label-grey);
  }
  .artwork {
    position: absolute;
    inset: 0;
  }
  .flag-edge { fill: var(--paper); stroke: var(--edge-grey); stroke-width: 0.8; }
  .fill-blue { fill: var(--brand-blue); }
  .fill-blue-mid { fill: var(--blue-mid); }
  .fill-blue-light { fill: var(--blue-light); }
  .fill-ink { fill: var(--ink); }
  .fill-paper { fill: var(--paper); }
  .ink-stroke { fill: none; stroke: var(--ink); }
  .pole { fill: var(--ink); }
  .stand-leg { stroke: var(--stand-grey); stroke-width: 1.6; stroke-linecap: round; }
  .brand-name {
    font-family: "Roboto", Arial, sans-serif;
    font-weight: 900;
    font-size: 21px;
    letter-spacing: 1px;
    fill: var(--ink);
  }
</style>
</head>
<body>
<main class="board">
  <p class="design-label" style="left:105px">DESIGN #1</p>
  <p class="design-label" style="left:382px">DESIGN #2</p>
  <p class="design-label" style="left:673px">DESIGN #3</p>
  <p class="design-label" style="left:947px">DESIGN #4</p>

  <svg class="artwork" width="1200" height="800" viewBox="0 0 1200 800" xmlns="http://www.w3.org/2000/svg">
    <defs>
      <symbol id="flag-stand" viewBox="0 0 130 580" width="130" height="580">
        <circle class="pole" cx="60" cy="7" r="7"/>
        <rect class="pole" x="56.5" y="8" width="7" height="478"/>
        <rect class="pole" x="58" y="486" width="4" height="46"/>
        <line class="stand-leg" x1="60" y1="532" x2="2" y2="537"/>
        <line class="stand-leg" x1="60" y1="532" x2="98" y2="521"/>
        <line class="stand-leg" x1="60" y1="532" x2="122" y2="553"/>
        <line class="stand-leg" x1="60" y1="532" x2="22" y2="566"/>
        <circle cx="60" cy="532" r="3" fill="#9a9a9a"/>
      </symbol>
      <clipPath id="flag-area"><rect width="240" height="145"/></clipPath>
    </defs>

    <use href="#flag-stand" x="25" y="133"/>
    <use href="#flag-stand" x="305" y="133"/>
    <use href="#flag-stand" x="584" y="133"/>
    <use href="#flag-stand" x="859" y="133"/>

    <g class="flag flag-swoosh" transform="translate(89 148)">
      <rect class="flag-edge" width="240" height="145"/>
      <g clip-path="url(#flag-area)">
        <path class="fill-blue" d="M0 0 H208 C198 8 188 10 172 10 H48 C28 10 14 24 0 55 Z"/>
        <path class="ink-stroke" stroke-width="6" d="M1 70 C18 26 28 10 50 9 L204 12"/>
        <path class="fill-blue" d="M240 82 V145 H30 C42 138 52 135 72 135 H188 C210 135 224 118 240 82 Z"/>
        <path class="ink-stroke" stroke-width="6" d="M239 78 C222 118 212 134 190 134 L64 137"/>
      </g>
      <rect class="fill-blue" x="62" y="63" width="14" height="14"/>
      <text class="brand-name" x="81" y="78">KESTREL</text>
    </g>

    <g class="flag flag-shards" transform="translate(370 148)">
      <rect class="flag-edge" width="240" height="145"/>
      <g clip-path="url(#flag-area)">
        <path class="fill-blue" d="M110 0 H240 V50 L232 82 L200 6 H110 Z"/>
        <path class="ink-stroke" stroke-width="3.5" d="M198 0 L214 30 M209 54 L236 106"/>
        <path class="fill-blue" d="M0 112 L10 64 L36 122 L128 140 V145 H0 Z"/>
        <path class="ink-stroke" stroke-width="3.5" d="M3 40 L30 92 M22 116 L40 145"/>
      </g>
      <rect class="fill-blue" x="62" y="63" width="14" height="14"/>
      <text class="brand-name" x="81" y="78">KESTREL</text>
    </g>

    <g class="flag flag-wave" transform="translate(649 148)">
      <rect class="flag-edge" width="240" height="145"/>
      <g clip-path="url(#flag-area)">
        <path class="fill-blue-light" d="M48 0 H240 V122 C236 64 232 24 202 14 C152 6 132 18 92 14 C70 12 58 6 48 0 Z"/>
        <path class="fill-blue-mid" d="M60 0 H240 V100 C236 54 228 20 200 8 C160 0 120 12 90 8 C76 6 68 4 60 0 Z"/>
        <path class="fill-blue-light" d="M0 12 V145 H176 C154 138 142 128 102 131 C62 134 30 140 16 124 C4 108 10 58 0 12 Z"/>
        <path class="fill-blue-mid" d="M0 30 V145 H150 C134 140 124 134 100 136 C60 140 22 146 10 130 C2 114 6 70 0 30 Z"/>
      </g>
      <rect class="fill-blue" x="62" y="63" width="14" height="14"/>
      <text class="brand-name" x="81" y="78">KESTREL</text>
    </g>

    <g class="flag flag-ring" transform="translate(921 148)">
      <rect class="fill-ink" width="242" height="145"/>
      <g clip-path="url(#flag-area)">
        <circle class="fill-blue" cx="121" cy="72" r="104"/>
        <circle class="fill-paper" cx="121" cy="72" r="92"/>
        <circle class="ink-stroke" stroke-width="3" cx="121" cy="72" r="84"/>
      </g>
      <rect class="fill-blue" x="62" y="63" width="14" height="14"/>
      <text class="brand-name" x="81" y="78">KESTREL</text>
    </g>
  </svg>
</main>
</body>
</html>
```